Brackwell Exteriors Needs a New Website!

We are an exteriors company specializing in vinyl siding, Corwin Maddox siding, aluminum soffit/fascia, trough. We do new construction work as well as renovations. We also build detached garages.
You can view our current website at www.brackwellfabricators.ca
I want to completely overhaul the website.
Our services are different now as we no longer do new home construction as well as we do not do the snow clearing.
I want to focus on 2 things in particular on the website:

1/ Exterior renovations

2/ Detached Garage construction.

I have included our logo in the attached files to use as well.

Some features we would like:

1/ Be able to easily attach a video from Clipverse/Reelio to highlight a product or service
2/ Quick chat or contact button that we can talk to a potential client quickly
3/ Meet the Team page that is interesting and fresh
4/ Place for us to put in helpful exterior tips/suggestions for homeowners.

Content is not important, but looking for the best design that will attract people once they click on our page and want to renovate with us.

Target Market(s)

People looking for renovations on their home, people looking to build a detached garage.

Industry/Entity Type

Residential Construction

Number of Pages Required

5+ page

Font styles to use
Sans Serif

Requirements
Must have
• Fresh and exciting home page.

Simple design. Don't want it over complicated or too much information to confuse the potential client.

Easy way to contact us.

Meet the team page that instills confidence
Nice to have
• Colour of website to go off our logo. Doesn't need to be an exact match, but something that goes well with our blue and grey.

```html
<!DOCTYPE html>
<html lang="en">
<head>
<meta charset="utf-8">
<title>Brackwell Exteriors</title>
<link href="https://fonts.googleapis.com/css2?family=Montserrat:wght@400;500;600;700&display=swap" rel="stylesheet">
<style>
:root{
  --blue:#1a6fc4;
  --blue-dark:#0f4f98;
  --navy:#132a46;
  --ink:#1b1f26;
  --grey:#5d6470;
  --pale:#eef5fc;
  --wave:#dfecf9;
  --white:#ffffff;
  --footer:#0d1c30;
}
*{margin:0;padding:0;box-sizing:border-box}
html,body{width:1200px;height:5111px;overflow:hidden}
body{position:relative;background:var(--pale);font-family:'Montserrat',sans-serif;color:var(--ink)}
.abs{position:absolute}
.center{text-align:center}
.btn{position:absolute;background:var(--blue);color:var(--white);font-size:12px;font-weight:700;letter-spacing:.5px;text-transform:uppercase;display:flex;align-items:center;justify-content:center;border-radius:3px}
.btn.light{background:var(--white);color:var(--blue)}
.section-title{position:absolute;left:0;width:1200px;text-align:center;font-size:28px;font-weight:700;letter-spacing:.5px}
.section-title span{color:var(--blue)}
.section-title::after{content:"";display:block;width:60px;height:3px;background:var(--blue);margin:6px auto 0}

/* waves */
.wave{position:absolute;background:var(--wave);border-radius:50%}

/* header */
.brand{display:flex;align-items:center;gap:10px;font-weight:700;color:var(--navy)}
.brand .dot{width:48px;height:48px;border-radius:50%;background:var(--blue)}
.brand .name{font-size:24px;letter-spacing:.5px}
.nav{position:absolute;top:36px;left:540px;display:flex;gap:38px;font-size:13px;font-weight:500;color:var(--white)}
.nav .active{color:var(--white);position:relative}
.nav .active::after{content:"";position:absolute;left:-6px;right:-6px;top:48px;height:3px;background:var(--blue)}

.hero{position:absolute;left:0;top:0;width:1200px;height:870px;clip-path:polygon(0 0,100% 0,100% 650px,0 870px);background:linear-gradient(180deg,#3c4f66 0%,#6b7c90 35%,#5a4a3e 60%,#2c3440 100%)}
.hero-title{position:absolute;top:515px;left:0;width:1200px;text-align:center;color:var(--white);font-size:40px;font-weight:600;letter-spacing:1px}

.service-photo{position:absolute;width:410px;height:410px;border-radius:50%}
.service-label{position:absolute;width:410px;text-align:center;font-size:21px;font-weight:700;line-height:31px;letter-spacing:.5px}

.about-sub{position:absolute;top:1266px;left:0;width:1200px;text-align:center;font-size:14px;color:var(--grey)}
.about-body{position:absolute;top:1300px;left:160px;width:880px;text-align:center;font-size:12.5px;line-height:24px;color:var(--grey)}

.video{position:absolute;left:140px;top:1522px;width:920px;height:454px;background:var(--white);padding:8px;box-shadow:0 6px 20px rgba(20,60,110,.12)}
.video .frame{width:100%;height:100%;background:linear-gradient(135deg,#8a8f94 0%,#c9cdd1 45%,#9aa0a6 70%,#b23a32 72%,#c9cdd1 76%)}

/* why choose */
.feature{position:absolute;width:330px}
.feature h3{font-size:16px;font-weight:700;letter-spacing:.3px;margin-bottom:6px}
.feature p{font-size:12px;line-height:21px;color:var(--grey)}
.feature.left{text-align:right}
.feature.blue h3{color:var(--blue)}
.icon-dot{position:absolute;width:76px;height:76px;border-radius:50%;background:#2b2f36;display:flex;align-items:center;justify-content:center}
.icon-dot.blue{background:var(--blue)}

.banner{position:absolute;left:142px;width:916px;border-radius:10px;overflow:hidden;color:var(--white);text-align:center}
.banner .kicker{position:absolute;left:0;width:100%;font-size:17px}
.banner .headline{position:absolute;left:0;width:100%;font-size:32px;font-weight:700;letter-spacing:1px}

.tile{position:absolute}
.work-card{position:absolute;left:142px;top:3262px;width:450px;height:403px;background:linear-gradient(160deg,#2d83d3,#1460ad);color:var(--white);text-align:center}
.work-card .inner{position:absolute;inset:14px;border:1px solid rgba(255,255,255,.5)}
.work-card h3{position:absolute;top:120px;left:30px;right:30px;font-size:19px;line-height:31px;font-weight:700}
.work-card p{position:absolute;top:208px;left:60px;right:60px;font-size:12px;line-height:21px}

.inquiry{position:absolute;left:142px;top:4110px;width:916px;height:485px;background:var(--white);border-radius:8px;box-shadow:0 10px 30px rgba(20,60,110,.1)}
.field{position:absolute;border:1px solid #dde3ea;font-size:11px;color:#7a828e;padding:14px 12px}
.chat{position:absolute;left:1113px;top:4282px;width:60px;height:60px;border-radius:50%;background:var(--white);box-shadow:0 4px 16px rgba(20,60,110,.2);display:flex;align-items:center;justify-content:center}

.footer-nav{position:absolute;top:4812px;left:0;width:1200px;display:flex;justify-content:center;gap:0;font-size:13px;font-weight:500}
.footer-nav span{padding:0 24px;border-right:1px solid #c5cfdb}
.footer-nav span:last-child{border-right:none}
.contact-col{position:absolute;top:4870px;width:300px;text-align:center}
.contact-col h4{font-size:13px;font-weight:700;margin:14px 0 6px}
.contact-col p{font-size:12px;line-height:19px;color:var(--ink)}
.bottom-bar{position:absolute;left:0;top:5040px;width:1200px;height:71px;background:var(--footer);color:#c7d2df;font-size:11.5px}
.social{position:absolute;top:24px;width:28px;height:28px;border-radius:50%}
</style>
</head>
<body>

<!-- background waves -->
<div class="wave" style="left:-300px;top:1380px;width:1800px;height:700px;transform:rotate(-8deg)"></div>
<div class="wave" style="left:-400px;top:2500px;width:1400px;height:900px;transform:rotate(10deg)"></div>
<div class="wave" style="left:-200px;top:4000px;width:1700px;height:600px;transform:rotate(-6deg)"></div>

<!-- hero -->
<div class="hero" role="img" aria-label="Two-storey house with shingle siding and stone accents under a light snowfall"></div>
<div class="abs brand" style="left:140px;top:18px">
  <div class="dot"></div>
  <div class="name" style="color:var(--white)">BRACKWELL EXTERIORS</div>
</div>
<nav class="nav">
  <span class="active">HOME</span><span>ABOUT US</span><span>SERVICES</span><span>MEET THE TEAM</span><span>CONTACT US</span>
</nav>
<h1 class="hero-title">EXPERIENCE THE BRACKWELL DIFFERENCE</h1>
<div class="btn" style="left:512px;top:580px;width:176px;height:38px">Get Started Today</div>

<!-- services -->
<div class="service-photo" style="left:168px;top:648px;background:radial-gradient(circle at 40% 40%,#e8e4dc,#a89a82 55%,#4d6a8a)" role="img" aria-label="House exterior under renovation with scaffolding"></div>
<div class="service-photo" style="left:618px;top:648px;background:radial-gradient(circle at 50% 35%,#dfe6ee,#b06a4a 55%,#5d8c4a)" role="img" aria-label="Completed detached garage with brick and siding"></div>
<div class="service-label" style="left:168px;top:1076px">EXTERIOR<br>RENOVATIONS</div>
<div class="service-label" style="left:618px;top:1076px">DETACHED GARAGE<br>CONSTRUCTION</div>

<!-- about -->
<h2 class="section-title" style="top:1200px">ABOUT <span>US</span></h2>
<p class="about-sub">We Are A People Looking For Renovations On Their Home, People Looking To Build A Detached Garage</p>
<p class="about-body">Lorem ipsum dolor sit amet, consectetuer adipiscing elit, sed diam nonummy nibh euismod tincidunt ut laoreet dolore magna aliquam erat volutpat. Ut wisi enim ad minim veniam, quis nostrud exerci tation ullamcorper suscipit lobortis nisl ut aliquip ex ea commodo consequat. Duis autem vel eum iriure dolor in hendrerit in vulputate velit esse molestie consequat, vel illum dolore eu feugiat nulla facilisis at vero eros et accumsan et iusto odio dignissim qui blandit praesent luptatum zzril delenit augue duis dolore te feugait nulla facilisi.</p>
<div class="btn" style="left:529px;top:1418px;width:142px;height:38px">Read More</div>

<!-- video -->
<div class="video">
  <div class="frame" role="img" aria-label="Video still of scaffolding along a house wall"></div>
</div>
<svg class="abs" style="left:563px;top:1711px" width="74" height="74" viewBox="0 0 74 74">
  <circle cx="37" cy="37" r="34" fill="#fff"/>
  <path d="M30 24 L52 37 L30 50 Z" fill="#1a6fc4"/>
</svg>
<svg class="abs" style="left:158px;top:1920px" width="884" height="16">
  <rect x="0" y="6" width="884" height="4" rx="2" fill="#fff"/>
  <rect x="0" y="6" width="138" height="4" rx="2" fill="#1a6fc4"/>
  <circle cx="138" cy="8" r="6" fill="#fff" stroke="#1a6fc4" stroke-width="3"/>
</svg>

<!-- why choose us -->
<h2 class="section-title" style="top:2054px">WHY <span>CHOOSE US?</span></h2>
<svg class="abs" style="left:420px;top:2140px" width="360" height="380" viewBox="0 0 360 380">
  <ellipse cx="180" cy="190" rx="165" ry="175" fill="none" stroke="#9aa5b3" stroke-width="1" stroke-dasharray="4 6"/>
  <circle cx="180" cy="190" r="120" fill="#cfe1f3"/>
  <circle cx="180" cy="190" r="100" fill="#fff"/>
  <circle cx="180" cy="190" r="42" fill="none" stroke="#1a6fc4" stroke-width="6"/>
</svg>
<div class="icon-dot" style="left:440px;top:2157px"><svg width="30" height="30"><rect x="4" y="5" width="22" height="18" fill="none" stroke="#fff" stroke-width="2"/><path d="M8 11h14M8 16h10" stroke="#fff" stroke-width="2"/></svg></div>
<div class="icon-dot blue" style="left:684px;top:2157px"><svg width="30" height="30"><path d="M6 26V12L15 5l9 7v14z" fill="none" stroke="#fff" stroke-width="2"/></svg></div>
<div class="icon-dot" style="left:380px;top:2292px"><svg width="30" height="30"><path d="M15 4l10 4v7c0 6-5 10-10 12C10 25 5 21 5 15V8z" fill="none" stroke="#fff" stroke-width="2"/></svg></div>
<div class="icon-dot" style="left:744px;top:2292px"><svg width="30" height="30"><rect x="4" y="6" width="18" height="12" rx="4" fill="none" stroke="#fff" stroke-width="2"/><circle cx="20" cy="22" r="4" fill="none" stroke="#fff" stroke-width="2"/></svg></div>
<div class="icon-dot" style="left:440px;top:2437px"><svg width="30" height="30"><circle cx="15" cy="15" r="7" fill="none" stroke="#fff" stroke-width="2"/><circle cx="15" cy="15" r="11" fill="none" stroke="#fff" stroke-width="2" stroke-dasharray="3 3"/></svg></div>
<div class="icon-dot" style="left:684px;top:2437px"><svg width="30" height="30"><circle cx="15" cy="12" r="6" fill="none" stroke="#fff" stroke-width="2"/><path d="M5 26h20" stroke="#fff" stroke-width="2"/></svg></div>

<div class="feature left" style="left:95px;top:2148px"><h3>GUARANTEED SATISFACTION</h3><p>We aren't happy unless you are. Along with a robust limited lifetime warranty on our work, we ensure you are satisfied even years after completion.</p></div>
<div class="feature blue" style="left:775px;top:2148px"><h3>CERTIFIED EXPERIENCE</h3><p>Having professionals do the job gives you the confidence that the job will be done right, on budget, and on time.</p></div>
<div class="feature left" style="left:32px;top:2288px"><h3>SAFETY CONSCIENCE</h3><p>COR certification, liability insurance, and WCB coverage on all workers gives you peace of mind that the job will be done safely.</p></div>
<div class="feature" style="left:838px;top:2288px"><h3>SUPERIOR COMMUNICATION</h3><p>Taking the time to explain the construction process and promptly answering the phone or email is what sets us apart from others.</p></div>
<div class="feature left" style="left:95px;top:2432px"><h3>UNRIVALLED QUALITY</h3><p>Our greatest asset is our unrivalled pursuit of a "top of the line" job each and every time.</p></div>
<div class="feature" style="left:775px;top:2432px"><h3>COMPETITIVE PRICING</h3><p>Although we offer the best in services, we won't blow your budget on the job. We also take credit cards in our renovations division.</p></div>

<!-- pride banner -->
<div class="banner" style="top:2632px;height:280px;background:linear-gradient(120deg,#1a6fc4,#0d5cae 60%,#1a78cf)" role="img" aria-label="Blue blueprint background">
  <div class="kicker" style="top:78px">Honest And Reliable Construction Service In Edmonton And Area.</div>
  <div class="headline" style="top:106px">We Take Pride In Each And Every Project</div>
</div>
<div class="btn light" style="left:512px;top:2800px;width:176px;height:38px">Get Started Today</div>

<!-- featured work -->
<h2 class="section-title" style="top:2982px">FEATURED <span>WORK</span></h2>
<div class="tile" style="left:142px;top:3055px;width:218px;height:195px;background:linear-gradient(180deg,#c9cfd6,#6f5c4b)" role="img" aria-label="House under construction"></div>
<div class="tile" style="left:372px;top:3055px;width:220px;height:195px;background:linear-gradient(180deg,#f4f4f4,#dadada)" role="img" aria-label="Floor plan drawing"></div>
<div class="tile" style="left:608px;top:3055px;width:450px;height:400px;background:linear-gradient(180deg,#4d6a8f 0%,#8d90a0 40%,#a46a3a 65%,#3f5a2f 100%)" role="img" aria-label="Modern timber house at dusk"></div>
<div class="work-card">
  <div class="inner"></div>
  <h3>Unrivalled Quality and Attention to Detail Turning Dreams into Reality</h3>
  <p>Lorem ipsum dolor sit amet, ipsu, ofte consectetuer adipiscing elit, sed diam nonummy nibh euismod tincidunt ut laoreet dolore magna aliquam erat volutpat Ut wisi enim...</p>
</div>
<div class="tile" style="left:608px;top:3473px;width:217px;height:192px;background:linear-gradient(180deg,#8a5a3c,#c9a98a)" role="img" aria-label="Interior wooden staircase"></div>
<div class="tile" style="left:840px;top:3473px;width:218px;height:192px;background:linear-gradient(180deg,#e2e4e6,#8c8f93)" role="img" aria-label="Modern grey kitchen"></div>

<!-- garage banner -->
<div class="banner" style="top:3753px;height:280px;background:linear-gradient(180deg,#2d3a2c,#5a4a3e 60%,#2a2a2a)" role="img" aria-label="Detached garage at evening">
  <div class="kicker" style="top:86px">Lorem ipsum dolor sit amet, Ipsum often consectetuer adipiscing elit</div>
  <div class="headline" style="top:112px">DETACHED GARAGE CONSTRUCTION</div>
</div>
<div class="btn light" style="left:512px;top:3924px;width:176px;height:38px">Get Started Today</div>

<!-- inquiry -->
<div class="inquiry">
  <h2 class="section-title" style="top:70px;width:916px">QUICK <span>INQUIRY</span></h2>
  <div class="field" style="left:60px;top:145px;width:388px;height:42px">Name*</div>
  <div class="field" style="left:468px;top:145px;width:390px;height:42px">Phone*</div>
  <div class="field" style="left:60px;top:202px;width:388px;height:42px">Email*</div>
  <div class="field" style="left:468px;top:202px;width:390px;height:42px">Choose a Service<span style="position:absolute;right:12px">&#8964;</span></div>
  <div class="field" style="left:60px;top:259px;width:798px;height:100px">Message*</div>
  <div class="btn" style="left:395px;top:372px;width:126px;height:38px">Submit</div>
</div>
<div class="chat"><svg width="30" height="30"><circle cx="13" cy="13" r="9" fill="none" stroke="#1a6fc4" stroke-width="2"/><circle cx="19" cy="19" r="7" fill="#fff" stroke="#1a6fc4" stroke-width="2"/></svg></div>

<!-- footer -->
<div class="abs brand" style="left:474px;top:4705px">
  <div class="dot"></div>
  <div class="name">BRACKWELL EXTERIORS</div>
</div>
<div class="footer-nav"><span>HOME</span><span>ABOUT US</span><span>SERVICES</span><span>MEET THE TEAM</span><span>CONTACT US</span></div>

<div class="contact-col" style="left:135px">
  <svg width="30" height="40"><rect x="7" y="3" width="16" height="32" rx="3" fill="none" stroke="#1a6fc4" stroke-width="2"/><circle cx="15" cy="30" r="1.5" fill="#1a6fc4"/></svg>
  <h4>PHONE</h4><p>+1 780-555-0143</p>
</div>
<div class="contact-col" style="left:450px">
  <svg width="30" height="40"><path d="M15 37C8 27 5 21 5 15a10 10 0 0 1 20 0c0 6-3 12-10 22z" fill="none" stroke="#1a6fc4" stroke-width="2"/><circle cx="15" cy="15" r="4" fill="none" stroke="#1a6fc4" stroke-width="2"/></svg>
  <h4>BRACKWELL EXTERIORS</h4><p>4720 Birchfield Rd #18, Alder<br>Park, AB T0X 2Q7, Canada</p>
</div>
<div class="contact-col" style="left:763px">
  <svg width="46" height="40"><rect x="3" y="7" width="40" height="28" fill="none" stroke="#1a6fc4" stroke-width="2"/><path d="M3 7l20 16 20-16" fill="none" stroke="#1a6fc4" stroke-width="2"/></svg>
  <h4>EMAIL</h4><p>info@brackwellfabricators.ca</p>
</div>

<div class="bottom-bar">
  <div class="abs" style="left:142px;top:29px">Copyright © 2020 BRACKWELL EXTERIORS. All Rights Reserved.</div>
  <div class="social" style="left:920px;background:#1a6fc4"></div>
  <div class="social" style="left:956px;background:#1a6fc4"></div>
  <div class="social" style="left:992px;background:#1a6fc4"></div>
  <div class="social" style="left:1028px;background:#1a6fc4"></div>
</div>

</body>
</html>
```